Building company buisness cards

We are looking for a sharp modern new look for our business cards.
We are a New Zealand based company that specialises in house and land packages.
We have attached a photo of the current logo and would like to see if it can be improved somehow if needed.
We are open to any colours but we have chosen green at this stage.
Feel free to change the font and make the logo smarter looking.
Play with the colours and see what looks best.

We want a card that looks so good know one will want to throw it away!

Target Market(s)

Home buyers

Industry/Entity Type

Building

Contact Information for Business Card

Derek Tolvane
0217394062
dtolvane@quillmarkhomesteads.co.nz
quillmarkhomesteads.co.nz

Font styles to use
Serif
Sans Serif

Colors

Designer to choose colors to be used in the design.

Requirements
Must have
• Logo and company name on one side, details on the other side
Nice to have
• Color codes for the original green are HEX #4a8028, RGB(74,128,40), CMYK(42,0,69,50)
• Round corners, Raised and/or spot UV

```html
<!DOCTYPE html>
<html lang="en">
<head>
<meta charset="utf-8">
<title>Quillmark Homesteads – Business Card</title>
<link rel="stylesheet" href="https://fonts.googleapis.com/css2?family=Roboto:wght@400;500&display=swap">
<style>
  :root {
    --backdrop: #2b2b2b;
    --card-white: #ffffff;
    --brand-green: #4a8028;
    --roof-grey: #565656;
    --text-white: #ffffff;
  }
  * { margin: 0; padding: 0; box-sizing: border-box; }
  html, body {
    width: 1125px;
    height: 1200px;
    overflow: hidden;
    background: var(--backdrop);
  }
  .sheet {
    position: relative;
    width: 1125px;
    height: 1200px;
  }
  .card {
    position: absolute;
    left: 145px;
    width: 800px;
    height: 456px;
    border-radius: 26px;
    overflow: hidden;
  }
  .card--front { top: 95px; background: var(--card-white); }
  .card--back { top: 611px; background: var(--brand-green); }

  .roof {
    position: absolute;
    inset: 0;
    width: 800px;
    height: 456px;
  }

  .company-name {
    position: absolute;
    left: 0;
    right: 0;
    display: flex;
    align-items: center;
    justify-content: center;
    gap: 14px;
    font-family: "Roboto", sans-serif;
    font-weight: 500;
    line-height: 1;
    white-space: nowrap;
  }
  .company-name__square {
    width: 18px;
    height: 18px;
    flex: none;
  }
  .company-name--front {
    top: 95px;
    font-size: 40px;
    letter-spacing: 3px;
    color: var(--brand-green);
  }
  .company-name--front .company-name__square { background: var(--brand-green); }
  .company-name--back {
    top: 204px;
    font-size: 44px;
    letter-spacing: 3px;
    color: var(--text-white);
  }
  .company-name--back .company-name__square { background: var(--text-white); }

  .contact {
    position: absolute;
    left: 0;
    right: 0;
    top: 300px;
    text-align: center;
    font-family: "Roboto", sans-serif;
    color: var(--text-white);
  }
  .contact__name {
    font-weight: 500;
    font-size: 27px;
    letter-spacing: 0.5px;
    margin-bottom: 14px;
  }
  .contact__line {
    font-weight: 400;
    font-size: 17px;
    line-height: 25px;
  }
  .contact__line--phone { font-size: 18px; }
</style>
</head>
<body>
<main class="sheet">
  <section class="card card--front" aria-label="Card front with contact details">
    <svg class="roof" viewBox="0 0 800 456" aria-hidden="true">
      <polygon points="0,405 400,192 800,405 800,430 400,217 0,430" fill="var(--brand-green)" stroke="var(--brand-green)" stroke-width="4" stroke-linejoin="round"/>
      <polyline points="0,434 400,221 800,434" fill="none" stroke="var(--card-white)" stroke-width="3"/>
      <polygon points="0,438 400,225 800,438 800,456 0,456" fill="var(--roof-grey)"/>
    </svg>
    <h1 class="company-name company-name--front"><span class="company-name__square"></span>QUILLMARK HOMESTEADS</h1>
    <div class="contact">
      <p class="contact__name">DEREK TOLVANE</p>
      <p class="contact__line contact__line--phone">(P) 0217394062</p>
      <p class="contact__line">dtolvane@quillmarkhomesteads.co.nz</p>
      <p class="contact__line">quillmarkhomesteads.co.nz</p>
    </div>
  </section>

  <section class="card card--back" aria-label="Card back with company name">
    <h2 class="company-name company-name--back"><span class="company-name__square"></span>QUILLMARK HOMESTEADS</h2>
  </section>
</main>
</body>
</html>
```